TA BRAMLEY BUSINESS CARD DESIGN PROJECT

We need to utilize our logo that was expertly created on PixelHarbor and now need to match this with a business card design.

```html
<!DOCTYPE html>
<html lang="en">
<head>
<meta charset="utf-8">
<title>TA Bramley Business Card</title>
<link rel="stylesheet" href="https://fonts.googleapis.com/css2?family=Montserrat:wght@400;500;700;800&display=swap">
<style>
  :root {
    --brand-blue: #1656a8;
    --card-white: #ffffff;
    --card-black: #1a1a1b;
    --backdrop: #3a3a3a;
    --text-light: #f2f2f2;
  }
  * { margin: 0; padding: 0; box-sizing: border-box; }
  html, body { width: 1200px; height: 900px; overflow: hidden; }
  body {
    background: var(--backdrop);
    font-family: "Montserrat", Arial, sans-serif;
    position: relative;
  }
  .card {
    position: absolute;
    width: 560px;
    height: 320px;
    border-radius: 22px;
    overflow: hidden;
    background: var(--card-white);
    box-shadow: 0 10px 28px rgba(0,0,0,0.45);
  }
  .card--front { left: 320px; top: 90px; }
  .card--back { left: 320px; top: 470px; }

  .wordmark {
    color: var(--brand-blue);
    font-weight: 800;
    letter-spacing: 0.08em;
    line-height: 1;
    display: flex;
    align-items: center;
    gap: 14px;
  }
  .wordmark__square {
    width: 0.7em; height: 0.7em;
    background: var(--brand-blue);
  }
  .card--front .wordmark {
    position: absolute;
    left: 0; right: 0; top: 0; bottom: 0;
    justify-content: center;
    font-size: 64px;
  }

  .card__shape { position: absolute; inset: 0; width: 100%; height: 100%; }

  .card--back .wordmark {
    position: absolute;
    right: 34px; top: 46px;
    font-size: 34px;
  }
  .holder {
    position: absolute;
    left: 0; top: 92px;
    display: flex;
    align-items: stretch;
  }
  .holder__bar { width: 22px; background: var(--brand-blue); margin-right: 12px; }
  .holder__name {
    color: var(--brand-blue);
    font-weight: 800;
    font-size: 21px;
    letter-spacing: 0.01em;
  }
  .holder__role { color: #222; font-size: 15px; font-weight: 500; margin-top: 2px; }

  .contact {
    position: absolute;
    left: 74px; top: 212px;
    color: var(--text-light);
    font-size: 12.5px;
    line-height: 1.4;
  }
  .contact__address { margin-bottom: 8px; }
  .contact__row { display: flex; align-items: center; gap: 8px; }
  .contact__icon { width: 12px; height: 12px; fill: var(--brand-blue); flex: none; }
</style>
</head>
<body>

  <section class="card card--front" aria-label="Card front">
    <div class="wordmark"><span class="wordmark__square"></span>TA BRAMLEY</div>
  </section>

  <section class="card card--back" aria-label="Card back">
    <svg class="card__shape" viewBox="0 0 560 320" preserveAspectRatio="none" aria-hidden="true">
      <path d="M0 320 L0 250 C80 200 150 170 260 160 C380 150 470 140 560 95 L560 320 Z" fill="var(--brand-blue)"/>
      <path d="M0 320 L0 262 C80 212 160 182 270 172 C390 162 480 150 560 108 L560 320 Z" fill="var(--card-black)"/>
      <path d="M10 240 C90 185 170 158 300 150 C190 160 110 190 10 240 Z" fill="var(--brand-blue)"/>
    </svg>

    <div class="wordmark"><span class="wordmark__square"></span>TA BRAMLEY</div>

    <div class="holder">
      <span class="holder__bar"></span>
      <div>
        <div class="holder__name">NORA WHITFIELD</div>
        <div class="holder__role">Managing Director</div>
      </div>
    </div>

    <div class="contact">
      <div class="contact__address">Your address, City<br>State, Zip 1234</div>
      <div class="contact__row">
        <svg class="contact__icon" viewBox="0 0 24 24" aria-hidden="true"><path d="M6.6 10.8a15 15 0 0 0 6.6 6.6l2.2-2.2a1 1 0 0 1 1-.25 11.4 11.4 0 0 0 3.6.6 1 1 0 0 1 1 1V20a1 1 0 0 1-1 1A17 17 0 0 1 3 4a1 1 0 0 1 1-1h3.5a1 1 0 0 1 1 1c0 1.25.2 2.45.6 3.6a1 1 0 0 1-.25 1z"/></svg>
        <span>123 456 789</span>
      </div>
      <div class="contact__row">
        <svg class="contact__icon" viewBox="0 0 24 24" aria-hidden="true"><path d="M2 5h20v14H2z M2 5l10 8 10-8" /></svg>
        <span>info@yourgmail.com</span>
      </div>
      <div class="contact__row">
        <svg class="contact__icon" viewBox="0 0 24 24" aria-hidden="true"><circle cx="12" cy="12" r="10"/></svg>
        <span>www.yourwebsite.com</span>
      </div>
    </div>
  </section>

</body>
</html>
```